New Fun, Positive, energised looking Business Card Needed for High Achiever Coach

I am looking for a two sided full colour business card. I am self employed and have recently re branded my 1-2-1 work re-vitalising high achievers. My target client base for these cards is therefore high achievers - usually aged 40 -55, they are often entrepreneurs, CEO or work in banking and finance and 2/3 are male. I work with them on 90 day or 6 month coaching programs to help them live their success in a healthier, more sustainable and fulfiiled way. They pay for this privately so though they are corporate types the cards need not look 'corporate'. I want to portray the idea of transformation, vitality and re-connecting.
You can get a feel for the look I like on my new website: morvenlisk.co.uk
I want to use this logo with strapline (Re-Vitalising High Achievers) (I purchased off Logoharbor) and font/ colours (the turquoise and green).
Details to include on the card:
www.morvenlisk.co.uk
+44 7915 302618
morven@morvenlisk.co.uk
skype: morvenlisk
I'd also like to include:
Do you struggle to switch off? Want to be healthier and feel fitter? Want closer relationships? More clarity over the direction you are headed? I can help you do these things using integrated mind-body techniques. Visit morvenlisk.co.uk TODAY to apply for a FREE Breakthrough session.
BUT if that is too much text for a card I am open to advice/ammendments.
Updates
Thanks for your design - I am considering them. PLease change the wording to :

```html
<!DOCTYPE html>
<html lang="en">
<head>
<meta charset="utf-8">
<title>Morven Lisk – Business Card</title>
<link rel="stylesheet" href="https://fonts.googleapis.com/css2?family=Ubuntu:ital,wght@0,400;0,500;0,700;1,400&display=swap">
<style>
  :root {
    --turquoise: #1aa3c8;
    --turquoise-deep: #0b86ad;
    --turquoise-light: #2bb4d8;
    --leaf-green: #5cb85c;
    --paper: #ffffff;
    --paper-shade: #e9e9e9;
    --backdrop: #d9d6d1;
    --ink-white: #ffffff;
  }
  * { box-sizing: border-box; margin: 0; padding: 0; }
  html, body {
    width: 1200px; height: 900px; overflow: hidden;
    background: var(--backdrop);
    font-family: "Ubuntu", sans-serif;
  }
  .canvas { position: relative; width: 1200px; height: 900px; }

  .card {
    position: absolute;
    width: 660px; height: 377px;
    border-radius: 4px;
    overflow: hidden;
    box-shadow: 0 6px 18px rgba(0,0,0,0.18);
  }

  /* Front */
  .card-front {
    left: 60px; top: 62px;
    background: linear-gradient(135deg, var(--paper) 35%, var(--paper-shade) 100%);
    display: flex; flex-direction: column;
  }
  .front-identity {
    flex: 1;
    display: flex; flex-direction: column; align-items: center; justify-content: center;
    gap: 14px;
  }
  .brand-name {
    display: flex; align-items: center; gap: 14px;
    font-weight: 700; font-size: 46px; color: var(--turquoise);
    letter-spacing: 0.5px;
  }
  .brand-dot {
    width: 26px; height: 26px; border-radius: 50%;
    background: var(--leaf-green);
  }
  .strapline {
    font-size: 20px; font-style: italic; color: var(--turquoise);
  }
  .accent-stripe { height: 9px; background: var(--leaf-green); }
  .contact-band {
    height: 66px;
    background: linear-gradient(180deg, var(--turquoise-light), var(--turquoise));
    display: flex; align-items: center; justify-content: space-between;
    padding: 0 22px;
    color: var(--ink-white); font-size: 13px;
  }
  .contact-item { display: flex; align-items: center; gap: 7px; white-space: nowrap; }
  .contact-icon { width: 16px; height: 16px; flex: none; }
  .contact-circle {
    width: 14px; height: 14px; border-radius: 50%; background: var(--ink-white); flex: none;
  }

  /* Back */
  .card-back {
    left: 480px; top: 470px;
    background: radial-gradient(ellipse at 60% 35%, var(--turquoise-light) 0%, var(--turquoise) 50%, var(--turquoise-deep) 100%);
    color: var(--ink-white);
    display: flex; flex-direction: column; align-items: center; justify-content: center;
    text-align: center;
    padding: 26px 34px;
  }
  .back-name {
    display: flex; align-items: center; gap: 10px;
    font-weight: 700; font-size: 30px; margin-bottom: 12px;
  }
  .back-dot { width: 18px; height: 18px; border-radius: 50%; background: var(--ink-white); }
  .back-strapline { font-size: 18px; font-weight: 500; margin-bottom: 16px; }
  .pitch { font-size: 13.5px; font-style: italic; line-height: 1.55; }
  .pitch p { margin: 0; }
  .pitch .pitch-close { margin-top: 8px; }
</style>
</head>
<body>
<main class="canvas">

  <section class="card card-front" aria-label="Business card front">
    <div class="front-identity">
      <div class="brand-name"><span class="brand-dot"></span>Morven Lisk</div>
      <div class="strapline">Re-Vitalising High Achievers</div>
    </div>
    <div class="accent-stripe"></div>
    <footer class="contact-band">
      <span class="contact-item">
        <svg class="contact-icon" viewBox="0 0 16 16"><path fill="#fff" d="M3.5 1.5 6 4 4.8 5.8c.8 1.9 2.4 3.6 4.4 4.4L11 9l2.5 2.5-1.6 2.3C7 13.5 2.5 9 2.2 4.1z"/></svg>
        +44 7915 302618
      </span>
      <span class="contact-item">
        <svg class="contact-icon" viewBox="0 0 16 16"><rect x="1.5" y="3.5" width="13" height="9" rx="1" fill="none" stroke="#fff" stroke-width="1.4"/><path d="M2 4l6 5 6-5" fill="none" stroke="#fff" stroke-width="1.4"/></svg>
        morven@morvenlisk.co.uk
      </span>
      <span class="contact-item">
        <svg class="contact-icon" viewBox="0 0 16 16"><circle cx="8" cy="8" r="6.3" fill="none" stroke="#fff" stroke-width="1.3"/><ellipse cx="8" cy="8" rx="2.7" ry="6.3" fill="none" stroke="#fff" stroke-width="1.1"/><path d="M1.8 8h12.4" stroke="#fff" stroke-width="1.1"/></svg>
        www.morvenlisk.co.uk
      </span>
      <span class="contact-item">
        <span class="contact-circle"></span>
        morvenlisk
      </span>
    </footer>
  </section>

  <section class="card card-back" aria-label="Business card back">
    <div class="back-name"><span class="back-dot"></span>Morven Lisk</div>
    <div class="back-strapline">Re-Vitalising High Achievers</div>
    <div class="pitch">
      <p>Do you struggle to switch off?</p>
      <p>Want to be healthier and feel fitter?</p>
      <p>Want closer relationships?</p>
      <p>More clarity over the direction you are headed?</p>
      <p class="pitch-close">I can help you do these things using integrated mind-body techniques.</p>
      <p>Visit morvenlisk.co.uk TODAY to apply for a FREE Breakthrough session.</p>
    </div>
  </section>

</main>
</body>
</html>
```